Heater product information sheets

I need the two product information sheets organized and laid out in a clean, easy to read attractive manner. These sheets are to advertise propane heaters for outdoor use and for wholesale to propane distributors, restaurants and homeowners that need to have propane heat as the winter ends and spring begins. They will be used for chilly evenings when people want to be outside eating, drinking and being social.

Target Market(s)

Restaurants, hospitality industry, special events, party rental companies, home owners with backyards

Font styles to use
Sans Serif

Requirements
Must have
• My logo in the document instead of t. Marlow and company
Nice to have
• I would like to see Fire illustrated coming up the heaters and on the round glass, show it up the middle of the glass tube propane heater.

```html
<!DOCTYPE html>
<html lang="en">
<head>
<meta charset="utf-8">
<title>Glass Tube Propane Heaters</title>
<link rel="stylesheet" href="https://fonts.googleapis.com/css2?family=Poppins:wght@400;500;600;700&display=swap">
<style>
  :root {
    --coral: #e85a45;
    --orange: #f6a23a;
    --peach: #fbd9b3;
    --ink: #2b2b2b;
    --muted: #444;
    --paper: #ffffff;
  }
  * { margin: 0; padding: 0; box-sizing: border-box; }
  html, body { width: 849px; height: 1200px; overflow: hidden; background: var(--paper); }
  body { font-family: "Poppins", sans-serif; color: var(--ink); }
  .sheet { position: relative; width: 849px; height: 1200px; overflow: hidden; background: var(--paper); }

  .blob { position: absolute; border-radius: 50%; }
  .blob-top { width: 260px; height: 260px; right: -90px; top: -70px; background: var(--orange); opacity: .85; }
  .blob-top-soft { width: 180px; height: 180px; right: 60px; top: 40px; background: var(--peach); opacity: .6; }
  .blob-heater { width: 280px; height: 280px; left: -80px; top: 400px; background: var(--orange); opacity: .9; }
  .blob-bottom { width: 300px; height: 300px; right: -110px; bottom: -110px; background: var(--orange); opacity: .85; }
  .blob-bottom-soft { width: 200px; height: 200px; right: 120px; bottom: -60px; background: var(--peach); opacity: .7; }

  .title { position: absolute; left: 85px; top: 40px; }
  .title-main { font-size: 52px; font-weight: 700; color: var(--coral); line-height: 1.05; }
  .title-sub { font-size: 34px; font-weight: 600; color: var(--ink); line-height: 1.2; }

  .heater { position: absolute; left: 100px; top: 170px; width: 170px; height: 450px; border-radius: 30px 30px 10px 10px;
    background: linear-gradient(180deg, #3a3a3a 0%, #f7b955 22%, #f08a2a 55%, #2d2d2d 78%, #1e1e1e 100%); }

  .specs { position: absolute; left: 335px; top: 150px; width: 470px; }
  .section-head { font-size: 28px; font-weight: 700; color: var(--coral); letter-spacing: .5px; }
  .spec-row { display: flex; justify-content: space-between; margin-top: 18px; }
  .spec { width: 110px; text-align: center; font-size: 12px; line-height: 1.35; color: var(--muted); }
  .spec svg { display: block; margin: 0 auto 8px; }

  .details { position: absolute; left: 335px; top: 340px; width: 470px; }
  .detail-list { list-style: none; margin-top: 14px; }
  .detail-list li { position: relative; padding-left: 26px; font-size: 16px; line-height: 1.45; margin-bottom: 7px; color: var(--ink); }
  .detail-list li::before { content: ""; position: absolute; left: 4px; top: 8px; width: 10px; height: 10px; border-radius: 50%; background: var(--orange); }

  .uses { position: absolute; left: 30px; top: 735px; display: flex; gap: 18px; }
  .use { width: 82px; text-align: center; font-size: 9.5px; font-weight: 600; line-height: 1.35; color: var(--muted); text-transform: uppercase; }
  .use svg { display: block; margin: 0 auto 8px; }

  .contact { position: absolute; left: 60px; top: 890px; }
  .contact-head { font-size: 26px; font-weight: 700; color: var(--coral); }
  .company { font-size: 19px; margin-top: 8px; }
  .contact-row { display: flex; gap: 40px; margin-top: 12px; }
  .contact-item { display: flex; align-items: center; gap: 10px; font-size: 17px; margin-top: 12px; }
  .contact-row .contact-item { margin-top: 0; }
  .dot-icon { width: 30px; height: 30px; border-radius: 50%; background: var(--orange); display: flex; align-items: center; justify-content: center; flex: none; }
</style>
</head>
<body>
<div class="sheet">
  <div class="blob blob-top"></div>
  <div class="blob blob-top-soft"></div>
  <div class="blob blob-heater"></div>
  <div class="blob blob-bottom-soft"></div>
  <div class="blob blob-bottom"></div>

  <header class="title">
    <h1 class="title-main">Glass Tube</h1>
    <h2 class="title-sub">Propane Heaters</h2>
  </header>

  <div class="heater" role="img" aria-label="Glass tube propane patio heater with flame glowing up the centre of the tube"></div>

  <section class="specs">
    <h3 class="section-head">SPECIFICATIONS</h3>
    <div class="spec-row">
      <div class="spec">
        <svg width="34" height="34" viewBox="0 0 34 34"><path d="M17 3c2 7 9 10 9 18a9 9 0 0 1-18 0c0-5 3-7 4-11 1 3 2 4 4 5 1-4 1-8 1-12z" fill="none" stroke="#e85a45" stroke-width="2"/></svg>
        Powerful<br>46,000 BTU
      </div>
      <div class="spec">
        <svg width="34" height="34" viewBox="0 0 34 34"><path d="M11 5h12l7 6-4 4-3-2v16H11V13l-3 2-4-4z" fill="none" stroke="#e85a45" stroke-width="2" stroke-linejoin="round"/></svg>
        Black Powder<br>Coated Finish
      </div>
      <div class="spec">
        <svg width="34" height="34" viewBox="0 0 34 34"><rect x="9" y="8" width="16" height="22" rx="6" fill="none" stroke="#e85a45" stroke-width="2"/><rect x="13" y="3" width="8" height="5" fill="none" stroke="#e85a45" stroke-width="2"/></svg>
        Uses 20 lbs.<br>Propane Tank
      </div>
      <div class="spec">
        <svg width="34" height="34" viewBox="0 0 34 34"><circle cx="17" cy="17" r="13" fill="none" stroke="#e85a45" stroke-width="2"/><path d="M11 17l4 4 8-8" fill="none" stroke="#e85a45" stroke-width="2"/></svg>
        CE, DS, AGA, CSA, with ETL certificate and ROHS approved
      </div>
    </div>
  </section>

  <section class="details">
    <h3 class="section-head">ADDITIONAL DETAILS</h3>
    <ul class="detail-list">
      <li>Commercial Quality</li>
      <li>For Outdoor Use Only</li>
      <li>Conforms to ANSI STD Z83.26-2014</li>
      <li>Certified to CSA STD 2.37-2014 Gas- fired outdoor infrared patio heaters</li>
      <li>Safety Auto Shut Off Switch</li>
      <li>Thermostatic Control</li>
      <li>Base Diameter 17" - Anti-Tip Design</li>
      <li>Standard Wheels - Tilt &amp; Move</li>
      <li>Run time: 8-10 hours with standard 20 lbs. Propane tank</li>
      <li>96" Tall</li>
      <li>Heating Area: 200 sq. ft</li>
    </ul>
  </section>

  <section class="uses">
    <div class="use">
      <svg width="44" height="36" viewBox="0 0 44 36"><path d="M4 32L22 6l18 26zM22 6v26M4 32h36" fill="none" stroke="#444" stroke-width="2" stroke-linejoin="round"/></svg>
      Rentals for live events
    </div>
    <div class="use">
      <svg width="44" height="36" viewBox="0 0 44 36"><path d="M6 28a16 16 0 0 1 32 0zM3 31h38M22 8v4" fill="none" stroke="#444" stroke-width="2"/><circle cx="22" cy="7" r="2" fill="#444"/></svg>
      Rentals for restaurants &amp; catering halls
    </div>
    <div class="use">
      <svg width="44" height="36" viewBox="0 0 44 36"><path d="M5 17L22 4l17 13M9 14v18h26V14M18 32v-9h8v9" fill="none" stroke="#444" stroke-width="2" stroke-linejoin="round"/></svg>
      Purchase for your home or business
    </div>
  </section>

  <section class="contact">
    <h3 class="contact-head">To Rent or Purchase:</h3>
    <p class="company">T. Marlow &amp; Company</p>
    <div class="contact-row">
      <div class="contact-item">
        <span class="dot-icon"><svg width="16" height="16" viewBox="0 0 16 16"><path d="M4 1l2 3-1.5 1.5a9 9 0 0 0 6 6L12 10l3 2-1 3C7 15 1 9 1 2z" fill="#fff"/></svg></span>
        555-318-2047
      </div>
      <div class="contact-item">
        <span class="dot-icon"><svg width="16" height="16" viewBox="0 0 16 16"><rect x="1.5" y="3.5" width="13" height="9" fill="none" stroke="#fff" stroke-width="1.5"/><path d="M1.5 4L8 9l6.5-5" fill="none" stroke="#fff" stroke-width="1.5"/></svg></span>
        hello@marlowheat.example
      </div>
    </div>
    <div class="contact-item">
      <span class="dot-icon"><svg width="16" height="16" viewBox="0 0 16 16"><path d="M8 15s5-5 5-9a5 5 0 0 0-10 0c0 4 5 9 5 9z" fill="#fff"/><circle cx="8" cy="6" r="2" fill="#f6a23a"/></svg></span>
      42 Orchard Lane Millbrook, NJ 07999
    </div>
  </section>
</div>
</body>
</html>
```